Commercial and Residential Paint Contractor needs website

We need a website for our residential painting, multi-family painting and commercial painting company. We paint interior and exterior of houses, apartments and commercial buildings. I would like an about us page, residential page, multi family page, commercial page and contact us. Need keywords added to website for seo opitimazation. I like this website https://www.wallcraftcrew.com/

Target Market(s)

General Contractors and commercial property managers

Coding

Coded - Design and coding required

Number of Pages Required

5+ page

Font styles to use
Sans Serif

Requirements
Must have
• I need SEO keywords on pages

```html
<!DOCTYPE html>
<html lang="en">
<head>
<meta charset="utf-8">
<title>Brightcoat Painting – Residential, Commercial &amp; Multi-family Painting</title>
<meta name="description" content="Residential painting, commercial painting and multi-family painting contractor. Interior and exterior painting for houses, apartments and commercial buildings.">
<link rel="stylesheet" href="https://fonts.googleapis.com/css2?family=Poppins:wght@400;500;600;700&family=Montserrat:wght@700;800&display=swap">
<style>
:root{
  --red:#c8203a;
  --navy:#1d3c8f;
  --blue:#1e8ae6;
  --ink:#1c1c2a;
  --text:#4a4a55;
  --muted:#8a8a94;
  --grey:#f1f1f3;
  --teal:#12a7b5;
  --yellow:#f3a81c;
  --green:#66b945;
  --orange:#e9562a;
  --dark:#15151f;
  --btn:linear-gradient(90deg,var(--red),var(--navy));
}
*{margin:0;padding:0;box-sizing:border-box}
html,body{width:1200px;height:4422px;overflow:hidden}
body{position:relative;font-family:"Poppins",sans-serif;color:var(--text);background:#fff;font-size:11px;line-height:1.6}
.abs{position:absolute}
a{color:inherit;text-decoration:none}
.btn{position:absolute;display:inline-flex;align-items:center;justify-content:center;height:26px;padding:0 22px;border-radius:13px;background:var(--btn);color:#fff;font-size:9.5px;font-weight:500;white-space:nowrap}
.photo{position:absolute;border-radius:8px}
.splash{position:absolute;border-radius:50%}
.h-section{position:absolute;left:0;width:1200px;text-align:center;font-weight:600;font-size:23px;color:var(--ink)}
.lead{position:absolute;left:340px;width:520px;text-align:center;font-size:9.5px;line-height:1.75}

/* header */
.site-header{position:absolute;top:0;left:0;width:1200px;height:86px;background:#fff}
.brand{position:absolute;left:197px;top:24px;display:flex;align-items:center;gap:8px;font-size:22px;font-weight:700;color:var(--navy);letter-spacing:.5px}
.brand-mark{width:14px;height:14px;background:var(--red)}
.top-contact{position:absolute;top:10px;left:698px;display:flex;gap:24px;font-size:10px;color:var(--ink);align-items:center}
.top-contact span{display:flex;align-items:center;gap:6px}
.socials{display:flex;gap:5px}
.socials i{width:9px;height:9px;border:1px solid #555;display:block}
.main-nav a{position:absolute;top:51px;font-size:9.5px;line-height:14px;color:var(--ink);white-space:nowrap}
.main-nav .active{color:var(--red);border-bottom:2px solid var(--red)}

/* hero */
.hero{position:absolute;top:86px;left:0;width:1200px;height:455px;background:linear-gradient(180deg,#5b4d44 0%,#6f625a 40%,#453a34 75%,#8f8780 100%)}
.hero-title{position:absolute;top:230px;left:0;width:1200px;text-align:center;font-family:"Montserrat",sans-serif;font-weight:800;font-size:40px;color:#fff;letter-spacing:1px}
.hero-sub{position:absolute;top:294px;left:330px;width:540px;text-align:center;font-size:12px;line-height:1.75;color:#fff}
.hero-dots{position:absolute;top:480px;left:586px;display:flex;gap:5px}
.hero-dots i{width:5px;height:5px;border-radius:50%;background:#fff;opacity:.6;display:block}
.hero-dots i.on{background:var(--red);opacity:1}

/* welcome */
.welcome-title{position:absolute;left:197px;top:618px;font-size:23px;font-weight:600;color:var(--ink)}
.welcome-text{position:absolute;left:197px;top:664px;width:390px;font-size:9.5px;line-height:1.75}
.features{position:absolute;left:195px;top:752px;display:flex;gap:28px}
.feature{display:flex;align-items:center;gap:8px;font-size:9px;font-weight:600;color:var(--ink);line-height:1.4}
.feature .ic{width:30px;height:30px;border-radius:50%;display:flex;align-items:center;justify-content:center}

/* services */
.services-bg{position:absolute;top:915px;left:0;width:1200px;height:1420px;background:linear-gradient(180deg,#efeff1 0,#fafafa 140px,#fff 300px)}
.svc-box{position:absolute;height:194px;background:var(--grey);border-radius:10px}
.svc-title{position:absolute;font-size:16px;font-weight:600;color:var(--ink)}
.svc-title b{color:var(--navy);font-weight:600;font-size:18px}
.svc-text{position:absolute;width:255px;font-size:9.5px;line-height:1.75}

/* feature grid */
.tile{position:absolute;width:300px;height:221px;color:#fff;text-align:center}
.tile h3{margin-top:56px;font-size:16px;font-weight:600;letter-spacing:.3px}
.tile p{width:240px;margin:6px auto 0;font-size:9px;line-height:1.75}
.tile .pill{display:inline-block;margin-top:16px;height:24px;line-height:24px;padding:0 26px;border-radius:12px;background:var(--navy);font-size:9px}

/* news */
.meta{position:absolute;left:196px;top:3182px;font-size:8.5px;color:var(--muted)}
.news-head{position:absolute;left:196px;top:3206px;width:455px;font-size:14px;font-weight:600;color:var(--ink);line-height:1.5}
.news-text{position:absolute;left:196px;top:3261px;width:455px;font-size:9.5px;line-height:1.75}
.latest{position:absolute;left:688px;top:2926px;width:316px;height:400px;background:#fff;border-radius:8px;box-shadow:0 2px 14px rgba(0,0,0,.08)}
.latest h4{margin-top:20px;text-align:center;color:var(--navy);font-size:15px;font-weight:600}
.latest-item{position:absolute;left:26px;width:264px;height:62px;display:flex;gap:12px;border-bottom:1px solid #e4e4e8}
.latest-item .thumb{width:89px;height:60px;border-radius:3px;flex:none}
.latest-item small{display:block;font-size:8px;color:var(--muted);margin-top:2px}
.latest-item p{font-size:9px;font-weight:600;color:var(--ink);line-height:1.55;margin-top:4px}

/* testimonials */
.testimonials{position:absolute;top:3413px;left:0;width:1200px;height:327px;background:linear-gradient(90deg,rgba(200,32,58,.92) 0%,rgba(120,60,150,.88) 50%,rgba(30,138,230,.95) 100%),linear-gradient(180deg,#6a5f73,#8f8a9c)}
.testimonials h2{position:absolute;top:52px;width:1200px;text-align:center;color:#fff;font-size:23px;font-weight:600}
.avatar{position:absolute;top:122px;left:569px;width:62px;height:62px;border-radius:50%;border:3px solid #fff;background:linear-gradient(135deg,#c9a48a,#7a5a48)}
.quote{position:absolute;top:196px;left:320px;width:560px;text-align:center;color:#fff;font-size:12px;line-height:1.6}
.stars{position:absolute;top:250px;width:1200px;text-align:center;color:#f6c322;font-size:11px;letter-spacing:1px}
.client{position:absolute;top:268px;width:1200px;text-align:center;color:#fff;font-size:12px}
.arrow{position:absolute;top:196px;color:#fff;font-size:18px}

/* brands */
.brand-row{position:absolute;top:3894px;left:196px;display:flex;gap:11px}
.brand-tile{width:124px;height:78px;background:#fff;box-shadow:0 1px 8px rgba(0,0,0,.08);display:flex;align-items:center;justify-content:center;font-size:15px;font-weight:600;color:var(--navy)}
.slider-dots{position:absolute;top:3998px;left:585px;display:flex;gap:4px}
.slider-dots i{width:4px;height:4px;border-radius:50%;background:#999;display:block}
.slider-dots i.on{background:var(--ink)}

/* footer */
.site-footer{position:absolute;top:4044px;left:0;width:1200px;height:326px;background:linear-gradient(90deg,#b81e3c 0%,#4b3a99 50%,#1a8ae8 100%);color:#fff}
.footer-logo{position:absolute;left:196px;top:51px;width:125px;height:48px;background:#fff;border-radius:3px;display:flex;align-items:center;justify-content:center;font-size:13px;font-weight:700;color:var(--navy)}
.footer-about{position:absolute;left:196px;top:118px;width:250px;font-size:9px;line-height:1.8}
.f-col{position:absolute;top:56px}
.f-col h5{font-size:11.5px;font-weight:600;margin-bottom:10px}
.f-col li{list-style:none;font-size:9px;line-height:21px}
.f-col li::before{content:"›";margin-right:8px}
.f-contact p{font-size:9px;line-height:1.8;margin-bottom:8px;width:220px}
.f-contact em{font-style:italic;font-weight:600}
.f-rule{position:absolute;top:224px;left:176px;width:848px;height:1px;background:rgba(255,255,255,.35)}
.f-label{position:absolute;top:262px;font-size:11.5px;font-weight:600;line-height:1.3}
.f-social{position:absolute;top:268px;left:338px;display:flex;gap:10px}
.f-social i{width:14px;height:14px;border:1.5px solid #fff;border-radius:2px;display:block}
.newsletter{position:absolute;top:262px;left:783px;width:221px;height:26px;border-radius:13px;border:1px solid #fff;display:flex;align-items:center}
.newsletter span{flex:1;padding-left:14px;font-size:8.5px;color:rgba(255,255,255,.8)}
.newsletter b{height:24px;width:62px;border-radius:12px;background:#fff;color:var(--navy);font-size:9px;font-weight:500;display:flex;align-items:center;justify-content:center}
.copyright{position:absolute;top:4370px;left:0;width:1200px;height:52px;background:var(--dark);color:#ccc;text-align:center;line-height:52px;font-size:9px}
</style>
</head>
<body>

<header class="site-header">
  <a class="brand" href="#"><span class="brand-mark"></span>BRIGHTCOAT</a>
  <div class="top-contact">
    <span><svg width="10" height="10" viewBox="0 0 24 24"><path fill="#333" d="M6.6 10.8a15 15 0 006.6 6.6l2.2-2.2c.3-.3.7-.4 1-.2 1.1.4 2.3.6 3.6.6.6 0 1 .4 1 1V20c0 .6-.4 1-1 1A17 17 0 013 4c0-.6.4-1 1-1h3.5c.6 0 1 .4 1 1 0 1.3.2 2.5.6 3.6.1.3 0 .7-.2 1z"/></svg>012-7654321</span>
    <span><svg width="10" height="10" viewBox="0 0 24 24"><path fill="none" stroke="#333" stroke-width="2" d="M3 5h18v14H3zM3 5l9 8 9-8"/></svg>info@brightcoatpainting.com</span>
    <span class="socials"><i></i><i></i><i></i><i></i></span>
  </div>
  <nav class="main-nav">
    <a class="active" style="left:505px">Home</a>
    <a style="left:552px">About Us</a>
    <a style="left:616px">Residential</a>
    <a style="left:687px">Commercial</a>
    <a style="left:762px">Multifamily</a>
    <a style="left:833px">Contact</a>
  </nav>
  <a class="btn" style="left:891px;top:46px;width:113px;height:24px;padding:0">Request a Quote</a>
</header>

<section class="hero" role="img" aria-label="Freshly painted kitchen interior with dark counter and white cabinets"></section>
<svg class="abs" style="left:0;top:505px" width="1200" height="40" viewBox="0 0 1200 40" aria-hidden="true"><path fill="#fff" d="M0 24 C120 10 200 30 320 16 S520 28 640 12 S860 30 980 14 S1120 26 1200 10 V40 H0Z"/></svg>
<h1 class="hero-title">RESIDENTIAL PAINTING</h1>
<p class="hero-sub">We are family owned and operated with over 10 years' experience. We pride our self in performing to the highest degree of workmanship standards.</p>
<a class="btn" style="left:542px;top:364px;height:24px">Find Out More &nbsp;→</a>
<div class="hero-dots"><i></i><i class="on"></i><i></i><i></i></div>

<section aria-label="Welcome">
  <div class="splash" role="img" aria-label="Light blue paint splash" style="left:178px;top:606px;width:60px;height:50px;background:radial-gradient(circle,#8fd3f5 0,rgba(143,211,245,0) 70%)"></div>
  <h2 class="welcome-title">Welcome</h2>
  <p class="welcome-text">We need a website for our residential painting, multi-family painting and commercial painting company. We paint interior and exterior of houses, apartments and commercial buildings. I would like an about us page, residential page, multifamily page, commercial page and contact us. Need keywords added to website for seo optimization.</p>
  <div class="features">
    <div class="feature"><span class="ic" style="background:var(--red)"><svg width="14" height="14" viewBox="0 0 24 24"><rect x="4" y="4" width="16" height="16" rx="2" fill="none" stroke="#fff" stroke-width="2"/></svg></span>Free Color<br>Consultation</div>
    <div class="feature"><span class="ic" style="background:var(--navy)"><svg width="14" height="14" viewBox="0 0 24 24"><path fill="none" stroke="#fff" stroke-width="2" d="M12 3s6 7 6 11a6 6 0 01-12 0c0-4 6-11 6-11z"/></svg></span>Flexible Scheduling<br>Option</div>
    <div class="feature"><span class="ic" style="background:#1fbf9c"><svg width="14" height="14" viewBox="0 0 24 24"><path fill="none" stroke="#fff" stroke-width="2.5" d="M5 12l5 5 9-10"/></svg></span>Maintain a Clean<br>Work Area</div>
  </div>
  <a class="btn" style="left:196px;top:815px;height:24px">Know About Us</a>
  <div class="photo" role="img" aria-label="Commercial gym interior with reclaimed wood feature wall" style="left:632px;top:594px;width:372px;height:271px;background:linear-gradient(135deg,#9a8f86,#6b5a4c 55%,#c8c4bf)"></div>
  <div class="splash" role="img" aria-label="Purple and pink paint splatter" style="left:1130px;top:720px;width:90px;height:180px;background:radial-gradient(ellipse,#d7a9f0 0,rgba(215,169,240,0) 70%)"></div>
</section>

<div class="services-bg"></div>
<section aria-label="Our Services">
  <h2 class="h-section" style="top:966px">Our Services</h2>
  <div class="splash" role="img" aria-label="Light blue paint splash" style="left:566px;top:960px;width:60px;height:50px;background:radial-gradient(circle,rgba(143,211,245,.8) 0,rgba(143,211,245,0) 70%)"></div>
  <p class="lead" style="top:1016px">Lorem ipsum is simply dummy text of printing has been the industry's standard dummy text, when an unknown printer took a galley of type and scrambled it to make a type specimen book.</p>

  <div class="svc-box" style="left:158px;top:1257px;width:1042px"></div>
  <div class="splash" role="img" aria-label="Navy paint splatter" style="left:220px;top:1110px;width:150px;height:140px;background:radial-gradient(circle,var(--navy) 0,var(--navy) 25%,rgba(29,60,143,0) 60%)"></div>
  <div class="photo" role="img" aria-label="White residential kitchen with pendant lights" style="left:493px;top:1085px;width:530px;height:328px;background:linear-gradient(135deg,#e9e8e6,#b9b6b2 60%,#6a625c)"></div>
  <h3 class="svc-title" style="left:196px;top:1288px"><b>01.</b> Residential Painting</h3>
  <p class="svc-text" style="left:196px;top:1323px">Lorem ipsum is simply dummy text of printing has been printer took a galley of type and scrambled it to make a type specimen book.</p>
  <a class="btn" style="left:196px;top:1388px;width:101px;height:24px">Read More</a>

  <div class="svc-box" style="left:0;top:1674px;width:1042px"></div>
  <div class="photo" role="img" aria-label="Commercial gym with graphic wall mural" style="left:177px;top:1502px;width:530px;height:328px;background:linear-gradient(180deg,#2a2a30,#55565e 50%,#3a3a40)"></div>
  <div class="splash" role="img" aria-label="Red paint splatter" style="left:800px;top:1530px;width:140px;height:140px;background:radial-gradient(circle,var(--red) 0,var(--red) 22%,rgba(200,32,58,0) 60%)"></div>
  <h3 class="svc-title" style="left:745px;top:1705px"><b>02.</b> Commercial Painting</h3>
  <p class="svc-text" style="left:745px;top:1740px">Lorem ipsum is simply dummy text of printing has been printer took a galley of type and scrambled it to make a type specimen book.</p>
  <a class="btn" style="left:745px;top:1805px;width:101px;height:24px">Read More</a>

  <div class="svc-box" style="left:158px;top:2091px;width:1042px"></div>
  <div class="splash" role="img" aria-label="Teal paint splatter" style="left:225px;top:1935px;width:160px;height:150px;background:radial-gradient(circle,#18c3a8 0,#18c3a8 24%,rgba(24,195,168,0) 60%)"></div>
  <div class="photo" role="img" aria-label="Multi-family apartment kitchen with crystal pendant lights" style="left:493px;top:1920px;width:530px;height:328px;background:linear-gradient(135deg,#efeeec,#c7c2bc 55%,#5e5650)"></div>
  <h3 class="svc-title" style="left:196px;top:2122px"><b>03.</b> Multi-family Painting</h3>
  <p class="svc-text" style="left:196px;top:2157px">Lorem ipsum is simply dummy text of printing has been printer took a galley of type and scrambled it to make a type specimen book.</p>
  <a class="btn" style="left:196px;top:2222px;width:101px;height:24px">Read More</a>
</section>

<section aria-label="Painting inspiration">
  <div class="tile" style="left:0;top:2356px;background:var(--teal)"><h3>INSPIRATOR</h3><p>Lorem ipsum is simply dummy text of printing has been printer took a galley of type and scrambled it to make a type specimen book.</p><span class="pill">Book Now</span></div>
  <div class="tile" role="img" aria-label="Turquoise painted room with framed art" style="left:300px;top:2356px;background:linear-gradient(180deg,#54d0e2,#b8e6ee)"></div>
  <div class="tile" style="left:600px;top:2356px;background:var(--yellow)"><h3>PICK YOUR COLOR</h3><p>Lorem ipsum is simply dummy text of printing has been printer took a galley of type and scrambled it to make a type specimen book.</p><span class="pill">Book Now</span></div>
  <div class="tile" role="img" aria-label="Homeowner choosing paint colour swatches" style="left:900px;top:2356px;background:linear-gradient(135deg,#d8dbe0,#7fa6b8 60%,#3e6470)"></div>
  <div class="tile" role="img" aria-label="Bright white interior with staircase railing" style="left:0;top:2577px;background:linear-gradient(135deg,#f2f2f2,#c9c9cc)"></div>
  <div class="tile" style="left:300px;top:2577px;background:var(--green)"><h3>FOLLOW THE TRENDS</h3><p>Lorem ipsum is simply dummy text of printing has been printer took a galley of type and scrambled it to make a type specimen book.</p><span class="pill">Book Now</span></div>
  <div class="tile" role="img" aria-label="Periwinkle painted living room with sofa" style="left:600px;top:2577px;background:linear-gradient(180deg,#6f86c9,#a8b6e0)"></div>
  <div class="tile" style="left:900px;top:2577px;background:var(--orange)"><h3>THE EXPERTS</h3><p>Lorem ipsum is simply dummy text of printing has been printer took a galley of type and scrambled it to make a type specimen book.</p><span class="pill">Book Now</span></div>
</section>

<section aria-label="Our News">
  <h2 class="h-section" style="top:2851px">Our News</h2>
  <div class="splash" role="img" aria-label="Light blue paint splash" style="left:570px;top:2845px;width:60px;height:50px;background:radial-gradient(circle,rgba(143,211,245,.8) 0,rgba(143,211,245,0) 70%)"></div>
  <div class="photo" role="img" aria-label="Freshly painted brick house exterior" style="left:196px;top:2926px;width:455px;height:239px;background:linear-gradient(180deg,#3d8fd8 0,#9cc7ee 35%,#8c7866 55%,#6d9a46 80%)"></div>
  <p class="meta">14 Jan, 2020 &nbsp;|&nbsp; News &nbsp;|&nbsp; Blog</p>
  <h3 class="news-head">Lorem Ipsum is simply dummy text of the printing &amp; typesetting industry. Lorem Ipsum has been the industry.</h3>
  <p class="news-text">Lorem Ipsum is simply dummy text of the printing and typesetting industry. Lorem Ipsum has been the industry's standard dummy text ever since the 1500s, when an unknown printer took a galley of type and scrambled it to make a type specimen book. It has survived not only five centuries.</p>
  <a class="btn" style="left:196px;top:3322px;width:101px;height:24px">Read More</a>

  <aside class="latest">
    <h4>Latest News</h4>
    <div class="latest-item" style="top:56px"><div class="thumb" role="img" aria-label="Wood feature wall" style="background:linear-gradient(135deg,#8a735f,#4f4035)"></div><div><small>14 Jan, 2020</small><p>Lorem Ipsum is simply dummy text of the industry industry...</p></div></div>
    <div class="latest-item" style="top:135px"><div class="thumb" role="img" aria-label="House exterior" style="background:linear-gradient(180deg,#5ea3e0,#8c7866 60%,#6d9a46)"></div><div><small>14 Jan, 2020</small><p>Lorem Ipsum is simply dummy text of the industry industry...</p></div></div>
    <div class="latest-item" style="top:214px"><div class="thumb" role="img" aria-label="House exterior" style="background:linear-gradient(180deg,#5ea3e0,#7b6a5a 60%,#6d9a46)"></div><div><small>14 Jan, 2020</small><p>Lorem Ipsum is simply dummy text of the industry industry...</p></div></div>
    <div class="latest-item" style="top:293px;border:0"><div class="thumb" role="img" aria-label="Kitchen interior" style="background:linear-gradient(135deg,#ddd,#6b625a)"></div><div><small>14 Jan, 2020</small><p>Lorem Ipsum is simply dummy text of the industry industry...</p></div></div>
  </aside>
  <a class="btn" style="left:803px;top:3302px;width:86px;height:24px">View All</a>
  <div class="splash" role="img" aria-label="Purple paint splatter" style="left:800px;top:3300px;width:260px;height:120px;background:radial-gradient(ellipse,rgba(196,140,240,.6) 0,rgba(196,140,240,0) 65%)"></div>
</section>

<section class="testimonials" aria-label="What Our Clients Say">
  <h2>What Our Clients Say</h2>
  <div class="avatar" role="img" aria-label="Client portrait"></div>
  <span class="arrow" style="left:280px">‹</span>
  <p class="quote">Mr. Holt went above and beyond to make sure that my repair request was expedited. Very professional and efficient!</p>
  <span class="arrow" style="left:908px">›</span>
  <div class="stars">★★★★★</div>
  <div class="client">Laura M</div>
</section>

<section aria-label="Work with trusted brands">
  <h2 class="h-section" style="top:3788px">Work with trusted brands</h2>
  <p class="lead" style="top:3836px">Lorem ipsum is simply dummy text of printing has been the industry's standard dummy text, when an unknown printer took a galley of type and scrambled it to make a type specimen book.</p>
  <div class="brand-row">
    <div class="brand-tile">Harbor Trust</div>
    <div class="brand-tile">Northline</div>
    <div class="brand-tile">Fair Pick</div>
    <div class="brand-tile">Slatewell</div>
    <div class="brand-tile">Orbit</div>
    <div class="brand-tile">Crossway</div>
  </div>
  <div class="slider-dots"><i></i><i></i><i class="on"></i><i></i></div>
</section>

<footer class="site-footer">
  <div class="footer-logo">BRIGHTCOAT</div>
  <p class="footer-about">We need a website for our residential painting, multi-family painting and commercial painting company. We paint interior and exterior of houses, apartments and commercial buildings.</p>
  <div class="f-col" style="left:482px"><h5>Our Services</h5><ul><li>Residential Painting</li><li>Multi-family Painting</li><li>Commercial Painting</li><li>Lead Removal</li><li>Texture Coatings</li></ul></div>
  <div class="f-col" style="left:651px"><h5>Quick Links</h5><ul><li>Home</li><li>About Us</li><li>Why Choose Us</li><li>Our News</li><li>Contact us</li></ul></div>
  <div class="f-col f-contact" style="left:807px"><h5>Contact Info</h5>
    <p><em>Address:</em> Lorem Ipsum has been the industry's 234 Lorem Ipsum text, FL 220</p>
    <p><em>Email:</em> info@brightcoatpainting.com</p>
    <p><em>Phone:</em> +012 - 7654321</p>
  </div>
  <div class="f-rule"></div>
  <div class="f-label" style="left:196px">Follow Us<br>On Social Network</div>
  <div class="f-social"><i></i><i></i><i></i><i></i></div>
  <div class="f-label" style="left:640px">Subscribe<br>On Our Newsletter</div>
  <div class="newsletter"><span>Enter Your Email</span><b>Join</b></div>
</footer>
<div class="copyright">© 2020 Brightcoat Painting. &nbsp;|&nbsp; All Rights Reserved</div>

</body>
</html>
```